Coastal Learner Bureau business cards

Australian company about to start offering its services. We recruit international students to come to study English, vocational education and postgraduate courses in Australia. We help them find the institution and select the right city they want to come to Australia. We are a young, online oriented and supportive agency. Our clients are between 18 and 35 years old, mainly University students, young professionals or people with work experience. We provide much more information that any other agency offer. We administrate a Facebook group with more than 11.000 members that daily ask questions about general information when coming to Australia, while they are here and even after they leave the country

Target Market(s)

International students from South America, Central America and Europe

Industry/Entity Type

Student

Contact Information for Business Card

Tomas Bilbrea
Managing Director
tomas@kelvarin.com.au
www.kelvoria.com.au
+61 491058264
Melbourne, Australia

Font styles to use
Serif
Sans Serif

Colors

Designer to choose colors to be used in the design.

Requirements
Must have
• Horizontal design
• Standard business card size and shape. If font uses green or yellow colours, they will have to match the ones from the logo
Nice to have
• UPDATE: Use the contents of the green image to design one of the card sides. Use our logo in the background of that side as watermark.
• Passport image, or immigration stamps. A picture of the Yarra River (from Melbourne) would be cool as well.
Should not have
• Non-standard business card size and shape
• Not black as the background colour of any sides as we are not a VIP agency or a hight class service. We are orientes to young people and they like colours, pictures, something attractive.
• Vertical design
• NO YELLOW or BLACK AS THE BACKGROUND COLOUR OF ANY SIDE OF THE BIZ CARD

```html
<!DOCTYPE html>
<html lang="en">
<head>
<meta charset="utf-8">
<title>Coastal Learner Bureau – Business Cards</title>
<link href="https://fonts.googleapis.com/css2?family=Roboto+Condensed:wght@500;700&family=Roboto:wght@400&display=swap" rel="stylesheet">
<style>
  :root{
    --stage:#2e2e2e;
    --paper:#f3f3f2;
    --brand-green:#0f5c3e;
    --brand-yellow:#e0b012;
    --ink-grey:#4a4a4a;
    --white:#ffffff;
    --rule:rgba(255,255,255,0.75);
  }
  *{box-sizing:border-box;margin:0;padding:0}
  html,body{width:1200px;height:960px;overflow:hidden}
  body{background:var(--stage);position:relative;font-family:"Roboto",Arial,sans-serif}

  .card{position:absolute;width:600px;height:343px}
  .card--front{left:314px;top:113px;background:var(--paper)}
  .card--back{left:311px;top:472px;background:var(--brand-green)}

  /* brand name block */
  .brand{position:absolute;display:flex;align-items:center;gap:10px;
    font-family:"Roboto Condensed",Arial,sans-serif;font-weight:700;line-height:1.02}
  .brand__dot{flex:none;border-radius:50%;background:var(--brand-yellow)}
  .card--front .brand{left:44px;top:78px;color:var(--brand-green);font-size:30px}
  .card--front .brand__dot{width:22px;height:22px}
  .card--back .brand{left:0;right:0;top:118px;justify-content:center;color:var(--white);font-size:40px}
  .card--back .brand__dot{width:28px;height:28px}

  /* identity */
  .identity{position:absolute;left:44px;top:240px;font-family:"Roboto Condensed",Arial,sans-serif}
  .identity__name{color:var(--brand-green);font-size:23px;font-weight:700;letter-spacing:.2px;text-transform:uppercase;line-height:26px}
  .identity__role{color:var(--brand-yellow);font-size:16px;font-weight:500;letter-spacing:.3px;text-transform:uppercase;line-height:20px}
  .identity__place{display:flex;align-items:center;gap:6px;margin-top:2px;
    font-family:"Roboto",Arial,sans-serif;color:var(--ink-grey);font-size:14.5px;line-height:20px}

  .contact{position:absolute;left:379px;top:246px;list-style:none;color:var(--ink-grey);font-size:14.5px}
  .contact li{display:flex;align-items:center;gap:6px;line-height:19.5px}
  .icon{width:13px;height:13px;flex:none;fill:var(--brand-green)}

  .tagline{position:absolute;left:62px;right:62px;top:298px;display:flex;align-items:center;gap:4px;
    color:var(--white);font-size:14.5px;white-space:nowrap}
  .tagline::before,.tagline::after{content:"";flex:1;height:1px}
  .tagline::before{background:linear-gradient(to right,transparent,var(--rule))}
  .tagline::after{background:linear-gradient(to left,transparent,var(--rule))}
</style>
</head>
<body>

<section class="card card--front" aria-label="Business card front">
  <div class="brand">
    <span class="brand__dot"></span>
    <span>Coastal Learner<br>Bureau</span>
  </div>

  <div class="identity">
    <p class="identity__name">Tomas Bilbrea</p>
    <p class="identity__role">Managing Director</p>
    <p class="identity__place">
      <svg class="icon" viewBox="0 0 24 24"><path d="M12 1a8 8 0 0 0-8 8c0 6 8 14 8 14s8-8 8-14a8 8 0 0 0-8-8zm0 11a3 3 0 1 1 0-6 3 3 0 0 1 0 6z"/></svg>
      Melbourne, Australia
    </p>
  </div>

  <ul class="contact">
    <li>
      <svg class="icon" viewBox="0 0 24 24"><path d="M6.6 10.8a15.1 15.1 0 0 0 6.6 6.6l2.2-2.2c.3-.3.7-.4 1-.2 1.1.4 2.3.6 3.6.6.6 0 1 .4 1 1V20c0 .6-.4 1-1 1A17 17 0 0 1 3 4c0-.6.4-1 1-1h3.5c.6 0 1 .4 1 1 0 1.3.2 2.5.6 3.6.1.3 0 .7-.2 1z"/></svg>
      +61 491058264
    </li>
    <li>
      <svg class="icon" viewBox="0 0 24 24"><path d="M2 5h20v14H2zm2 2v.5l8 5 8-5V7l-8 5z"/></svg>
      tomas@kelvarin.com.au
    </li>
    <li>
      <svg class="icon" viewBox="0 0 24 24"><path d="M12 2a10 10 0 1 0 0 20 10 10 0 0 0 0-20zm-1 17.9A8 8 0 0 1 4.2 10L9 14.8v1a2 2 0 0 0 2 2zm6.9-2.5A2 2 0 0 0 16 16h-1v-3a1 1 0 0 0-1-1H8v-2h2a1 1 0 0 0 1-1V7h2a2 2 0 0 0 2-2v-.4a8 8 0 0 1 2.9 12.8z"/></svg>
      www.kelvoria.com.au
    </li>
  </ul>
</section>

<section class="card card--back" aria-label="Business card back">
  <div class="brand">
    <span class="brand__dot"></span>
    <span>Coastal Learner Bureau</span>
  </div>
  <p class="tagline">Hacemos más por ti!</p>
</section>

</body>
</html>
```